Teach English in China Website Redesign Needed

We recruit native English speakers from the US, UK, etc. who want to teach English as a foreign language in schools in China. Our target customer is college educated, age 22-28 and they love to travel. We prefer designs with bright colors and lots of photos. We want to keep all the text on our current homepage, BrightLanternPost.com. We are open to changing our logo. A competitor's page that we like is pinemeadowtutors.com because of their bright colors, photos and use of white space. We are happy to give you a dofollow link and design credit on our homepage. The use of included photos is optional. We need at least a home page design and a standard blog post design.
Target Market(s)
Our target customer is college educated, age 22-28 and they love to travel. Half of our customers are kindergarten teachers. Half of our customers are male.
Logo Text
Bright Lantern Post
Requirements
Must have
- Bright colors
Should not have
- Our homepage must not look crowded. Use white space effectively.

```html
<!DOCTYPE html>
<html lang="en">
<head>
<meta charset="utf-8">
<title>Bright Lantern Post – Teach English in China</title>
<link href="https://fonts.googleapis.com/css2?family=Montserrat:wght@400;500;600;700&family=Open+Sans:wght@400;600;700&display=swap" rel="stylesheet">
<style>
:root{
  --red:#d7141a;
  --ink:#222;
  --text:#555;
  --muted:#777;
  --line:#bbb;
  --white:#fff;
  --footer:#111;
}
*{box-sizing:border-box;margin:0;padding:0}
html,body{width:1200px;height:2975px;overflow:hidden}
body{position:relative;background:var(--white);font-family:"Open Sans",Arial,sans-serif;color:var(--text)}
.block{position:absolute;left:0;width:1200px}

.topbar{top:0;height:44px;background:var(--red);display:flex;align-items:center;justify-content:space-between;padding:0 100px}
.topbar-links{display:flex;gap:26px;font-size:12px;color:var(--white);white-space:nowrap}
.topbar-social{display:flex;gap:18px}
.topbar-social span{width:12px;height:12px;border-radius:50%;background:var(--white);display:block}

.header{top:44px;height:108px;display:flex;align-items:center;justify-content:space-between;padding:0 100px}
.brand{display:flex;align-items:center;gap:10px;font-family:"Montserrat",sans-serif;font-weight:700;font-size:21px;color:var(--red);text-transform:uppercase;letter-spacing:.3px;white-space:nowrap}
.brand-mark{width:18px;height:18px;background:var(--red)}
.main-nav{display:flex;gap:62px;font-family:"Montserrat",sans-serif;font-size:17px;font-weight:500;color:var(--ink);white-space:nowrap}

.hero{top:152px;height:506px;background:linear-gradient(180deg,#3d3a34 0%,#544637 45%,#2f3a28 100%);text-align:center;color:var(--white)}
.hero-title{padding-top:176px;font-family:"Montserrat",sans-serif;font-weight:500;font-size:36px;line-height:62px;letter-spacing:1.5px}
.btn-outline{display:inline-block;border:2px solid var(--white);color:var(--white);font-family:"Montserrat",sans-serif;font-weight:600;font-size:20px;letter-spacing:.5px;padding:10px 44px;border-radius:3px;white-space:nowrap}
.hero .btn-outline{margin-top:22px}

.section-title{font-family:"Montserrat",sans-serif;font-weight:700;font-size:28px;color:var(--red);text-align:center;letter-spacing:.5px}

.intro{top:712px}
.intro-body{width:950px;margin:26px auto 0;text-align:center;font-size:12.5px;line-height:21px;color:var(--muted)}
.intro-body p{margin-bottom:21px}
.divider{top:1051px;left:312px;width:576px;height:1px;background:var(--line)}

.highlights-photo{top:1077px;left:99px;width:462px;height:345px;background:linear-gradient(160deg,#8f9aa3 0%,#4b5866 45%,#6f6556 100%)}
.highlights{top:1128px;left:620px;width:500px}
.highlights .section-title{text-align:left}
.highlight-list{list-style:none;margin-top:16px;font-size:12.5px;color:var(--text)}
.highlight-list li{height:26.5px;display:flex;align-items:center;gap:10px;white-space:nowrap}
.highlight-list svg{flex:none}

.job{top:1487px;height:377px;background:linear-gradient(180deg,#3b3631 0%,#4e4436 55%,#2c2a24 100%);text-align:center;color:var(--white)}
.job .section-title{color:var(--white);padding-top:62px}
.job-body{width:930px;margin:22px auto 0;font-size:16px;line-height:26px}
.job .btn-outline{margin-top:30px;font-size:18px;padding:10px 38px}

.testimonials{top:1910px}
.testimonial-card{position:absolute;top:2029px;width:504px;height:248px;border:1px solid #999;background:var(--white)}
.testimonial-card.first{left:79px}
.testimonial-card.second{left:619px}
.testimonial-photo{position:absolute;top:-46px;left:31px;width:143px;height:143px;background:linear-gradient(180deg,#3a3a3a,#1c1c1c)}
.testimonial-card.second .testimonial-photo{background:linear-gradient(180deg,#d9d9d9,#8a8a8a)}
.testimonial-name{position:absolute;top:50px;left:187px;font-family:"Montserrat",sans-serif;font-size:24px;font-weight:500;color:var(--red);white-space:nowrap}
.testimonial-date{position:absolute;top:84px;left:187px;font-size:11.5px;color:var(--ink)}
.testimonial-quote{position:absolute;top:122px;left:30px;right:30px;font-size:12.3px;line-height:21px;color:var(--text);text-align:justify}

.blog{top:2344px}
.blog-card{position:absolute;top:2435px;width:292px;height:278px}
.blog-card.post-one{left:99px}
.blog-card.post-two{left:453px}
.blog-card.post-three{left:807px}
.blog-thumb{height:228px}
.post-one .blog-thumb{background:linear-gradient(160deg,#d88aa0,#8f6fa8)}
.post-two .blog-thumb{background:linear-gradient(180deg,#f4f4f4,#cfe0a8)}
.post-three .blog-thumb{background:linear-gradient(180deg,#f3c21c,#d94a1a)}
.blog-caption{height:50px;background:var(--red);color:var(--white);font-family:"Montserrat",sans-serif;font-weight:600;font-size:14px;line-height:20px;display:flex;align-items:center;justify-content:center;text-align:center;padding:0 14px}

.newsletter{top:2776px;height:147px;background:var(--red);color:var(--white)}
.newsletter-title{position:absolute;top:38px;left:99px;font-family:"Montserrat",sans-serif;font-size:30px;font-weight:500}
.newsletter-text{position:absolute;top:90px;left:99px;font-size:16px}
.newsletter-form{position:absolute;top:60px;left:706px;display:flex}
.newsletter-input{width:280px;height:40px;border:1px solid rgba(255,255,255,.6);color:rgba(255,255,255,.8);font-size:12px;padding:0 14px;display:flex;align-items:center}
.newsletter-btn{width:116px;height:40px;background:var(--white);color:var(--ink);font-weight:700;font-size:16px;display:flex;align-items:center;justify-content:center}

.footer{top:2923px;height:52px;background:var(--footer);color:var(--white);font-size:11px;display:flex;align-items:center;justify-content:center}
</style>
</head>
<body>

<div class="block topbar">
  <nav class="topbar-links"><span>Job Board</span><span>Apply</span><span>Blog</span><span>Hire a Teacher</span><span>About Us</span></nav>
  <div class="topbar-social" aria-hidden="true"><span></span><span></span><span></span><span></span><span></span><span></span></div>
</div>

<header class="block header">
  <div class="brand"><span class="brand-mark"></span>Bright Lantern Post</div>
  <nav class="main-nav"><span>Home</span><span>Available Jobs</span><span>Apply Online</span><span>Blog</span><span>FAQ</span></nav>
</header>

<section class="block hero" role="img" aria-label="Photo of a traditional Chinese pavilion with stone steps among trees">
  <h1 class="hero-title">FREE CHINESE CLASSES 2 HOURS PER WEEK<br>WITH MOST JOBS</h1>
  <span class="btn-outline">JOIN TODAY</span>
</section>

<section class="block intro">
  <h2 class="section-title">TEACH ENGLISH IN CHINA</h2>
  <div class="intro-body">
    <p>Want to teach English in China? Do you enjoy teaching children or adults? Would you like the adventure of teaching in China for a year? Then we have the perfect job for you! We are seeking English speakers from the US, UK, Canada, Ireland, Australia, New Zealand and South Africa to teach English in China for a year (or longer if you wish). We recruit for hundreds of schools all over China such as Northstar English, Harbor Lane English, Redfield English, Maple Bridge English, Sunny Steps, Little Oak Kids, Silver Pear, public schools, international schools, universities, and more.</p>
    <p>imageedit_2_3503556638Don't want to fly to China alone? No problem, fly over with other new teachers and our American Director, Marla Jennings. She'll help you get settled and adjusted to Chinese culture. We take EXCELLENT care of our teachers with ongoing American and local support for your entire year in China.</p>
    <p>A Bachelor's degree and experience is recommended, but a degree is not required to teach kindergarten. If you have a Bachelor's degree, you also have the option to teach older children and adults. Also, more good news is that you do NOT need to know how to speak Chinese. Also, we provide FREE TEFL / TESOL 120-hour online certification to all the teachers we place.</p>
  </div>
</section>
<div class="block divider"></div>

<div class="block highlights-photo" role="img" aria-label="Aerial photo of a large teapot-shaped glass building by a lake"></div>
<section class="block highlights">
  <h2 class="section-title">OUR HIGHLIGHTS</h2>
  <ul class="highlight-list">
    <li><svg width="6" height="9" viewBox="0 0 6 9"><path d="M1 1l4 3.5L1 8" fill="none" stroke="#555" stroke-width="1.4"/></svg>Competitive compensation: 7000-9000 RMB/month, up to 18,000 RMB</li>
    <li><svg width="6" height="9" viewBox="0 0 6 9"><path d="M1 1l4 3.5L1 8" fill="none" stroke="#555" stroke-width="1.4"/></svg>Teach private English lessons after work for 250 RMB/hr</li>
    <li><svg width="6" height="9" viewBox="0 0 6 9"><path d="M1 1l4 3.5L1 8" fill="none" stroke="#555" stroke-width="1.4"/></svg>Airfare reimbursement: 5000 RMB at end of completed 1 year contract</li>
    <li><svg width="6" height="9" viewBox="0 0 6 9"><path d="M1 1l4 3.5L1 8" fill="none" stroke="#555" stroke-width="1.4"/></svg>Free TESOL / TEFL training and certification</li>
    <li><svg width="6" height="9" viewBox="0 0 6 9"><path d="M1 1l4 3.5L1 8" fill="none" stroke="#555" stroke-width="1.4"/></svg>Invitation letter so you can apply for a visa</li>
    <li><svg width="6" height="9" viewBox="0 0 6 9"><path d="M1 1l4 3.5L1 8" fill="none" stroke="#555" stroke-width="1.4"/></svg>Airport pickup</li>
    <li><svg width="6" height="9" viewBox="0 0 6 9"><path d="M1 1l4 3.5L1 8" fill="none" stroke="#555" stroke-width="1.4"/></svg>5-day work week, 25 hours teaching per week plus some office hours</li>
    <li><svg width="6" height="9" viewBox="0 0 6 9"><path d="M1 1l4 3.5L1 8" fill="none" stroke="#555" stroke-width="1.4"/></svg>20 paid holidays</li>
    <li><svg width="6" height="9" viewBox="0 0 6 9"><path d="M1 1l4 3.5L1 8" fill="none" stroke="#555" stroke-width="1.4"/></svg>Free Chinese classes 2 hours per week with most jobs</li>
  </ul>
</section>

<section class="block job" role="img" aria-label="Photo of a Chinese temple courtyard with golden roofs">
  <h2 class="section-title">JOB DESCRIPTION</h2>
  <p class="job-body">We are seeking English speakers from the US, UK, Canada, Ireland, Australia, New Zealand and South Africa to teach English in China for a year. A Bachelor's degree and experience is recommended, but if you want to work in a kindergarten, you can teach English in China without a degree. If you have a Bachelor's degree, you also have the option to teach older children and adults. Also, more good news is that you do NOT need to know how to speak Chinese.</p>
  <span class="btn-outline">CURRENT JOB OPENINGS</span>
</section>

<section class="block testimonials">
  <h2 class="section-title">TESTIMONIALS</h2>
</section>
<div class="testimonial-card first">
  <div class="testimonial-photo" role="img" aria-label="Portrait photo of a smiling young man"></div>
  <div class="testimonial-name">Owen Castell</div>
  <div class="testimonial-date">January 2, 2017</div>
  <p class="testimonial-quote">Marla was extremely helpful during the entire process. Moving to another country is a very challenging ordeal and having someone like Marla on your side makes all the difference. She's continued to be incrediblyafter arriving, fielding every one of my questions and following up with helpful suggestions. She has been a critical part of the process!</p>
</div>
<div class="testimonial-card second">
  <div class="testimonial-photo" role="img" aria-label="Black and white photo of a teacher with children"></div>
  <div class="testimonial-name">Priya Delacroix</div>
  <div class="testimonial-date">December 21, 2016</div>
  <p class="testimonial-quote">As soon as we got in touch, Marla guided me through every step of the process. I have had THE BEST experience under her guidance. Marla has been amazing at finding the best jobs out there. I would not hesitate to recommend her to anyone! Read More......</p>
</div>

<section class="block blog">
  <h2 class="section-title">RECENT BLOG POSTS</h2>
</section>
<div class="blog-card post-one">
  <div class="blog-thumb" role="img" aria-label="Screenshot of Chinese learning apps on a phone"></div>
  <div class="blog-caption">Basic Chinese Greetings</div>
</div>
<div class="blog-card post-two">
  <div class="blog-thumb" role="img" aria-label="Chart ranking countries by English proficiency"></div>
  <div class="blog-caption">How China Can Get Enough English Language Teachers</div>
</div>
<div class="blog-card post-three">
  <div class="blog-thumb" role="img" aria-label="Banner image of world landmarks for an ESL teachers forum"></div>
  <div class="blog-caption">Leo's ESL Lounge for the Best TEFL TESOL Teach Abroad Jobs</div>
</div>

<section class="block newsletter">
  <h2 class="newsletter-title">Our Newsletter</h2>
  <p class="newsletter-text">Sign up for our newsletter and know our latest post</p>
  <div class="newsletter-form">
    <div class="newsletter-input">enter your email id</div>
    <div class="newsletter-btn">Subscribe</div>
  </div>
</section>

<footer class="block footer">2017 © Bright Lantern Post. All Rights Reserved. Privacy Policy</footer>

</body>
</html>
```